Candle Rental Business seeks new website design

We need a new website design for a Candle hire business. The business rents out pillar candles for events such as weddings and corporate events. Our main target market is weddings. The business name is Hire a Lantern. The business name does not have a logo design.

We would like a website that is light in colours and creates a warm atmosphere. The design needs to be elegant and upmarket. There are different size candles that we hire out, ranging from 10cm diameter to 20cm diameter, flat, tall etc. All our candles are white in colour. Its just the size that differs.

We would also like to include a section for hiring out decor such as glassvases, candlebras, overlays and chairs sachets, chair covers. However, this is not the businesses main focus but an additional offering to customers.

Target Market(s)

Wedding venues and brides. Corporate events. School dances.

Industry/Entity Type

Hospitality

Logo Text

Hire a Lantern

Number of Pages Required

1 page

Font styles to use
Sans Serif
Script

Requirements
Must have
• Pictures of pillar candles. Plain white candles. The website must centre around candles.
Nice to have
• Different examples of candle centrepieces
Should not have
• Pictures must not be of brides. Pictures of surrounding is perferable.

```html
<!DOCTYPE html>
<html lang="en">
<head>
<meta charset="utf-8">
<title>Hire a Lantern</title>
<link href="https://fonts.googleapis.com/css2?family=Roboto+Slab:wght@300;400;500&family=Kaushan+Script&display=swap" rel="stylesheet">
<style>
:root{
  --gold:#e0ab2c;
  --rust:#c4532a;
  --footer:#c45e29;
  --green:#8aa63a;
  --band:#f5f1e7;
  --text:#6e6e6e;
  --dark:#444;
  --white:#fff;
  --social-a:#3a5ba0;
  --social-b:#2aa3e6;
  --social-c:#1a73b5;
  --social-d:#d2412f;
}
*{margin:0;padding:0;box-sizing:border-box}
html,body{width:768px;height:1200px;overflow:hidden}
body{position:relative;background:var(--white);font-family:"Roboto Slab","Rockwell","Georgia",serif;color:var(--text)}
.abs{position:absolute}
.hero{left:0;top:0;width:768px;height:349px;background:radial-gradient(ellipse at 40% 30%,#1f7fb0 0%,#124a78 35%,#0b1e3a 70%,#1a1410 100%)}
.hero-glow{left:0;top:180px;width:768px;height:169px;background:linear-gradient(180deg,rgba(0,0,0,0),rgba(120,60,20,.45))}
.nav{left:84px;top:0;width:600px;height:42px;background:var(--gold)}
.nav a{position:absolute;top:14px;color:var(--white);font-size:10.5px;text-decoration:none;font-weight:300}
.brand{left:296px;top:0;width:160px;height:81px;background:var(--white);border-radius:0 0 80px 80px;display:flex;align-items:center;justify-content:center;color:var(--rust);font-size:15px;padding-bottom:10px}
.brand-dot{width:8px;height:8px;border-radius:50%;background:var(--gold);margin-right:6px}
.headline{left:0;top:156px;width:768px;text-align:center;font-family:"Kaushan Script",cursive;font-size:33px;color:var(--white);font-weight:400}
.thumb{top:281px;width:85px;height:44px;border:2px solid var(--white)}
.thumb-pointer{left:279px;top:274px}
.section-title{font-weight:300;font-size:16px;color:var(--dark)}
.section-title span{color:var(--rust)}
.about-title{left:0;top:373px;width:768px;text-align:center}
.about-text{left:84px;top:408px;width:600px;text-align:center;font-size:8.8px;line-height:15.6px;font-weight:300}
.band{left:0;top:484px;width:768px;height:338px;background:var(--band)}
.card{background:var(--white)}
.card h3{position:absolute;font-weight:400;font-size:16px;color:var(--rust)}
.card p{position:absolute;font-size:7.4px;line-height:13.2px;font-weight:300}
.btn{position:absolute;background:var(--green);color:var(--white);font-size:7.5px;padding:0 10px;height:16px;line-height:16px;font-weight:300}
.photo{position:absolute}
.gallery-title{left:84px;top:844px}
.g{width:127px;height:72px}
.quote{left:524px;top:857px;width:160px;height:176px;background:var(--gold)}
.avatar{left:578px;top:844px;width:52px;height:52px;border-radius:50%;border:2px solid var(--white);background:radial-gradient(circle at 50% 40%,#c9a58a,#4a3326)}
.quote p{position:absolute;left:12px;top:48px;width:136px;text-align:center;font-size:7.3px;line-height:13.2px;color:var(--white);font-weight:300}
.quote .name{position:absolute;left:0;top:133px;width:160px;text-align:center;color:var(--rust);font-size:9.5px}
.dots{position:absolute;top:161px;height:2px}
.footer{left:0;top:1056px;width:768px;height:144px;background:var(--footer);color:var(--white)}
.footer .label{position:absolute;top:24px;font-size:12px;color:var(--gold)}
.social{position:absolute;top:48px;width:19px;height:19px}
.rule{position:absolute;left:84px;top:86px;width:600px;height:1px;background:rgba(255,255,255,.3)}
.flinks{position:absolute;left:0;top:102px;width:768px;text-align:center;font-size:8.5px}
.flinks span{margin:0 5px}
.copy{position:absolute;left:0;top:119px;width:768px;text-align:center;font-size:8px}
</style>
</head>
<body>
<div class="abs hero" role="img" aria-label="Candlelit event hall with blue lighting, branches and white pillar candles on tables"></div>
<div class="abs hero-glow"></div>
<nav class="abs nav">
  <a style="left:23px">Home</a><a style="left:82px">About Us</a><a style="left:154px">Services</a>
  <a style="left:394px">Products</a><a style="left:465px">Gallery</a><a style="left:528px">Contact Us</a>
</nav>
<div class="abs brand"><span class="brand-dot"></span>Hire a Lantern</div>
<h1 class="abs headline">Meaningful gift at a friendly price point</h1>
<svg class="abs thumb-pointer" width="12" height="8"><polygon points="0,8 6,1 12,8" fill="#fff"/></svg>
<div class="abs thumb" style="left:242px;background:linear-gradient(135deg,#1c6fa0,#0c2b4e)" role="img" aria-label="Blue lit candle hall"></div>
<div class="abs thumb" style="left:342px;background:linear-gradient(135deg,#3a2410,#a8752e)" role="img" aria-label="White pillar candles glowing"></div>
<div class="abs thumb" style="left:442px;background:linear-gradient(135deg,#c98a4b,#efe6dc)" role="img" aria-label="Candle lighting at a table"></div>

<h2 class="abs section-title about-title">About <span>Hire a Lantern</span></h2>
<p class="abs about-text">We are a family owned and operated company and began making decorative candles for all occasions. All of our candles are individually hand made in our candle studio, situated in Harrowby, outside Kelmont. Our wax is local and of a very high quality, and dripless! Our wax is also made with a high melting point, which means it will not melt or bend in hot temperatures.</p>

<div class="abs band"></div>
<div class="abs card" style="left:84px;top:509px;width:224px;height:295px">
  <div class="photo" style="left:12px;top:11px;width:201px;height:120px;background:linear-gradient(160deg,#d9d6d0,#f4f2ee 50%,#9ec6d4)" role="img" aria-label="White pillar candles on a set table"></div>
  <h3 style="left:12px;top:143px">Hire Candles</h3>
  <p style="left:12px;top:167px;width:202px">Do you love using candles for your events but tired of sorting old used candles or buying expensive candles. Believe it or not you can now rent candles.All our candles come in different sizes and heights.You can add the ambience of candlelight to your event of wedding ceremony without the worry over dripping wax or open candle flames.</p>
  <div class="btn" style="left:13px;top:266px">Read More</div>
</div>
<div class="abs card" style="left:320px;top:509px;width:364px;height:141px">
  <h3 style="left:12px;top:7px">Personalised Candles</h3>
  <p style="left:12px;top:35px;width:210px">Hire a Lantern provides the opportunity to give a thoughtful, meaningful gift at a friendly price point. This unique gift conveys the time and care you put into creating it. The recipient will enjoy the beautiful presentation and be reminded of the sentiment...</p>
  <div class="btn" style="left:13px;top:112px">Read More</div>
  <div class="photo" style="left:230px;top:10px;width:124px;height:124px;background:linear-gradient(150deg,#e8e8e6,#f7f2ea 60%,#d9a4b8)" role="img" aria-label="Personalised candles in glass jars"></div>
</div>
<div class="abs card" style="left:320px;top:662px;width:364px;height:142px">
  <h3 style="left:12px;top:7px">Décor Hire</h3>
  <p style="left:12px;top:36px;width:215px">We hire a selection of overlays, chair sachets and chair covers as well as glassware and candelabras to compliment your décor.</p>
  <div class="btn" style="left:13px;top:86px">Read More</div>
  <div class="photo" style="left:232px;top:12px;width:120px;height:119px;background:radial-gradient(circle at 50% 60%,#e9e4c8,#5f7a3a 55%,#3a1e1a)" role="img" aria-label="Floral candle centrepiece with glassware"></div>
</div>

<h2 class="abs section-title gallery-title">Our <span>Photo Gallery</span></h2>
<div class="abs g" style="left:84px;top:878px;background:linear-gradient(135deg,#6b4a2a,#e8ddd0)" role="img" aria-label="Candelabras with white candles"></div>
<div class="abs g" style="left:223px;top:878px;background:linear-gradient(135deg,#1c6fa0,#0c2b4e)" role="img" aria-label="Blue lit reception hall"></div>
<div class="abs g" style="left:362px;top:878px;background:linear-gradient(135deg,#2a1a0c,#9c7238)" role="img" aria-label="Pillar candle glowing"></div>
<div class="abs g" style="left:84px;top:962px;background:linear-gradient(135deg,#3a1f0c,#c8924a)" role="img" aria-label="Tall white candles on a table"></div>
<div class="abs g" style="left:223px;top:962px;background:linear-gradient(135deg,#1a0f08,#b07a48)" role="img" aria-label="Candle centrepieces with flowers"></div>
<div class="abs g" style="left:362px;top:962px;background:linear-gradient(135deg,#6a4a30,#e7e2da)" role="img" aria-label="Candle lighting ceremony setting"></div>

<div class="abs quote">
  <p>"There are many variations of passages of Lorem Ipsum available, but the majority have suffered alteration in some form, by injected humour, or randomised words which don't look even slightly believable."</p>
  <div class="name">Marcus Ellery</div>
  <div class="dots" style="left:51px;width:18px;background:#fff"></div>
  <div class="dots" style="left:71px;width:18px;background:rgba(255,255,255,.5)"></div>
  <div class="dots" style="left:91px;width:18px;background:rgba(255,255,255,.5)"></div>
</div>
<div class="abs avatar" role="img" aria-label="Customer portrait"></div>

<footer class="abs footer">
  <div class="label" style="left:84px">Location</div>
  <div style="position:absolute;left:85px;top:44px;font-size:9px;line-height:13.6px">Simply dummy text printing<br>typesetting AT 12356</div>
  <div style="position:absolute;left:0;top:30px;width:768px;text-align:center;font-size:11.5px;color:var(--gold)">+123 555 0190</div>
  <div style="position:absolute;left:0;top:46px;width:768px;text-align:center;font-size:12.5px;font-weight:500">hello@lanternhire.com</div>
  <div class="label" style="right:84px">Follow us</div>
  <div class="social" style="left:586px;background:var(--social-a)"></div>
  <div class="social" style="left:612px;background:var(--social-b)"></div>
  <div class="social" style="left:638px;background:var(--social-c)"></div>
  <div class="social" style="left:665px;background:var(--social-d)"></div>
  <div class="rule"></div>
  <div class="flinks"><span>Home</span>|<span>About Us</span>|<span>Services</span>|<span>Products</span>|<span>Gallery</span>|<span>Contact Us</span></div>
  <div class="copy">© 2016 Hire a Lantern, All Rights Reserved</div>
</footer>
</body>
</html>
```